"Vine Hollow Excursions" is a top notch Santa Barbara County Wine Tour company.

We provide scenic, boutique and custom wine tours. I need the card to be clean and classy. I will provide our logo. I would like the logo to cover the back side of the card as an option and would like to see a couple color options other then our signature green and gold. I would like to see some creative options and let the designers come up with options.
I need cards for myself and my team. The final design should communicate "An authentic and boutique wine tour experience"
Please use my website for reference www.vinehollowexcursions.example

Target Market(s)

We have a wide range of clients from millennials to baby boomers

Industry/Entity Type

Tour

Contact Information for Business Card

Contact info:
Dale Morton
805-219-6384
info@vinehollowexcursions.example
vinehollowexcursions.example

Colors

Designer to choose colors to be used in the design.

Requirements
Must have
• my logo
Nice to have
• *I would like to have the backside side with the logo and the company statement
• "An authentic and boutique wine tour experience" as an option.
• *I would also like to see what the designers can create!
• *I would like to see an option that incorporates or social: instagram, yelp, trip advisor
Should not have
• I do not want it too busy.

```html
<!DOCTYPE html>
<html lang="en">
<head>
<meta charset="utf-8">
<title>Vine Hollow Excursions – Business Card</title>
<link rel="stylesheet" href="https://fonts.googleapis.com/css2?family=Cinzel:wght@400;600&family=Jost:wght@400&family=Open+Sans:wght@400&display=swap">
<style>
  :root {
    --backdrop: #2a2a2a;
    --paper: #f2f2f1;
    --vine-green: #235c3c;
    --gold: #a48a63;
    --ink: #3b3b3b;
    --white: #ffffff;
    --badge-tan: #c9b48e;
    --badge-green: #4f8a3a;
    --badge-red: #d6332b;
  }
  * { box-sizing: border-box; margin: 0; padding: 0; }
  html, body { width: 1200px; height: 960px; overflow: hidden; }
  body { background: var(--backdrop); position: relative; }

  .card {
    position: absolute;
    width: 600px;
    height: 343px;
    box-shadow: 0 4px 10px rgba(0,0,0,.45);
    text-align: center;
  }
  .card--front { left: 314px; top: 113px; background: var(--paper); }
  .card--back  { left: 311px; top: 472px; background: var(--vine-green); }

  .brand-name {
    position: absolute;
    left: 0; right: 0;
    font-family: "Cinzel", serif;
    font-weight: 400;
    letter-spacing: 1px;
  }
  .card--front .brand-name { top: 125px; font-size: 27px; color: var(--gold); }
  .card--back .brand-name  { top: 170px; font-size: 30px; color: var(--white); }

  .brand-mark {
    display: block;
    width: 44px; height: 44px;
    margin: 0 auto 14px;
    border-radius: 50%;
  }
  .card--front .brand-mark { background: var(--vine-green); }
  .card--back .brand-mark  { background: var(--white); }
  .card--front .brand-name { top: 72px; }
  .card--back .brand-name  { top: 96px; }

  .holder-name {
    position: absolute;
    left: 0; right: 0; top: 222px;
    font-family: "Cinzel", serif;
    font-weight: 600;
    font-size: 24px;
    color: var(--vine-green);
  }
  .contact {
    position: absolute;
    left: 0; right: 0;
    font-family: "Jost", sans-serif;
    font-size: 16px;
    color: var(--ink);
  }
  .contact--line { top: 260px; }
  .contact--web  { top: 280px; }
  .contact .label { color: var(--vine-green); }

  .social {
    position: absolute;
    top: 31px; right: 30px;
    display: flex; gap: 4px;
  }
  .social span {
    width: 31px; height: 31px;
    border-radius: 6px;
  }
  .social .badge-photo  { background: var(--badge-tan); }
  .social .badge-travel { background: var(--badge-green); }
  .social .badge-review { background: var(--badge-red); }

  .tagline {
    position: absolute;
    left: 0; right: 0; top: 293px;
    font-family: "Open Sans", sans-serif;
    font-size: 15px;
    color: var(--white);
  }
</style>
</head>
<body>
  <section class="card card--front" aria-label="Card front">
    <div class="brand-name"><span class="brand-mark"></span>VINE HOLLOW EXCURSIONS</div>
    <div class="holder-name">DALE MORTON</div>
    <p class="contact contact--line"><span class="label">P.</span> 805-219-6384 <span class="label">E.</span> info@vinehollowexcursions.example</p>
    <p class="contact contact--web">www.vinehollowexcursions.example</p>
  </section>

  <section class="card card--back" aria-label="Card back">
    <div class="social" aria-label="Social listings">
      <span class="badge-photo"></span>
      <span class="badge-travel"></span>
      <span class="badge-review"></span>
    </div>
    <div class="brand-name"><span class="brand-mark"></span>VINE HOLLOW EXCURSIONS</div>
    <p class="tagline">An authentic &amp; boutique wine tour experience</p>
  </section>
</body>
</html>
```